Business Card Design

Looking for business card designs for a new business. there will be two cards of the same design (both lots of information below in contact info). We would like the logo diagonally across the card with the information split above and below the logo similar to sketch. happy to look at similar alternatives
Please use same colours as in logo design

Industry/Entity Type

Business

Contact Information for Business Card

Dwight Halloran
mob - 0491 738 204
ph - 02 6148 3920
fax - 02 6148 3975
email - dwight@kestrelbeams.com.au
14 Larkmoor Road, Brackenvale NSW 2391

Colin Marchetti
mob - 0438 912 557
ph - 02 6148 3920
fax - 02 6148 3975
email - colin@kestrelbeams.com.au

```html
<!DOCTYPE html>
<html lang="en">
<head>
<meta charset="utf-8">
<title>Kestrel Beams – Business Cards</title>
<link href="https://fonts.googleapis.com/css2?family=Open+Sans:wght@400;600;700&display=swap" rel="stylesheet">
<style>
  :root {
    --teal: #1f7f7c;
    --ink: #1a1a1a;
    --card: #ffffff;
    --backdrop: #e9e7e3;
    --edge: #2b2b2b;
  }
  * { margin: 0; padding: 0; box-sizing: border-box; }
  html, body { width: 1145px; height: 1200px; overflow: hidden; }
  body {
    background: var(--backdrop);
    font-family: "Open Sans", Arial, sans-serif;
    color: var(--ink);
    position: relative;
  }
  .card {
    position: absolute;
    background: var(--card);
    border: 1px solid var(--edge);
    overflow: hidden;
  }
  .card--front { left: 26px; top: 41px; width: 943px; height: 539px; }
  .card--back  { left: 170px; top: 615px; width: 945px; height: 538px; }

  .front-band { position: absolute; left: 0; top: 0; width: 140px; height: 539px; }

  .wordmark {
    position: absolute;
    display: flex;
    align-items: center;
    gap: 14px;
    font-weight: 700;
    color: var(--ink);
    white-space: nowrap;
    letter-spacing: -1px;
  }
  .wordmark__square { display: block; background: var(--teal); }
  .card--front .wordmark { left: 112px; top: 88px; font-size: 64px; line-height: 1; }
  .card--front .wordmark__square { width: 48px; height: 48px; }
  .card--back .wordmark { left: 0; right: 0; top: 210px; justify-content: center; font-size: 78px; line-height: 1; }
  .card--back .wordmark__square { width: 56px; height: 56px; }

  .contact-list {
    position: absolute;
    left: 108px; top: 289px;
    list-style: none;
    font-size: 23px;
    line-height: 35.5px;
  }
  .contact-list li { display: flex; align-items: center; gap: 6px; }
  .contact-list svg { width: 17px; height: 17px; fill: var(--teal); flex: none; }
  .address {
    position: absolute;
    left: 110px; top: 455px;
    font-size: 23px;
  }
  .person-name {
    position: absolute;
    right: 21px; top: 292px;
    font-size: 29px;
    font-weight: 700;
    color: var(--teal);
  }
  .website {
    position: absolute;
    left: 0; right: 0; top: 422px;
    text-align: center;
    font-size: 29px;
    letter-spacing: 2.5px;
  }
  .website strong { font-weight: 600; }
</style>
</head>
<body>

<section class="card card--front">
  <svg class="front-band" viewBox="0 0 140 539" aria-hidden="true">
    <path d="M0 0 H119 C 10 150, 10 390, 112 539 H0 Z" fill="var(--teal)"/>
    <path d="M119 0 C 10 150, 10 390, 112 539" fill="none" stroke="#fff" stroke-width="6"/>
    <path d="M124 0 C 15 150, 15 390, 117 539" fill="none" stroke="var(--edge)" stroke-width="1.5"/>
  </svg>

  <div class="wordmark"><span class="wordmark__square"></span>Kestrel Beams</div>

  <ul class="contact-list">
    <li><svg viewBox="0 0 16 16"><circle cx="8" cy="8" r="7.5" fill="none" stroke="var(--teal)" stroke-width="1.4"/><path d="M5 4l2 2-1 1.2c.6 1.3 1.5 2.2 2.8 2.8L10 9l2 2-1.4 1.4C7.5 12 4 8.5 3.6 5.4z"/></svg>02 6148 3920</li>
    <li><svg viewBox="0 0 16 16"><path d="M4.5 1h7v14h-7z M6 3v5h4V3z M6 9.5h1.2v1.2H6z M8.8 9.5H10v1.2H8.8z M6 12h1.2v1.2H6z M8.8 12H10v1.2H8.8z" fill-rule="evenodd"/></svg>0438 912 557</li>
    <li><svg viewBox="0 0 16 16"><path d="M4 2h8v4H4z M1 6.5h14V13H1z M3 14h10v1H3z"/></svg>02 6148 3975</li>
    <li><svg viewBox="0 0 16 16"><path d="M1 7l7-4 7 4v7H1z M2.5 7.4L8 10.5l5.5-3.1L8 4.5z" fill-rule="evenodd"/></svg>colin@kestrelbeams.com.au</li>
  </ul>
  <p class="address">14 Larkmoor Road, Brackenvale NSW 2391</p>

  <h1 class="person-name">Colin Marchetti</h1>
</section>

<section class="card card--back">
  <div class="wordmark"><span class="wordmark__square"></span>Kestrel Beams</div>
  <p class="website">www.<strong>kestrelbeams</strong>.com.au</p>
</section>

</body>
</html>
```